Musician looking for catchy Web Design for promotion

My name is Brenna Coyle. I'm an Irish musician who plays the tin whistle and the flute. I'm also the leader of a traditional Irish music and dance ensemble called Gather the Willows (www.gatherthewillows-example.com) and for the past 30 years, I've toured the world performing thousands of concerts. I run an annual cruise (www.brennacoylevoyage-example.com) that I would like a link to, and I'm also I'm organizing tours to Ireland that I would like a page set up for. I'm looking for a website to promote my tours and my music.
Updates

Hello Graphic Designers, I am only looking for the design of the home page to make my decision. Thank you. Brenna

Target Market(s)

Music fans of Irlsh and World Music

Industry/Entity Type

Entertainment Industry

Number of Pages Required

5+ page

Requirements
Must have
• I'm looking for a catchy design that shows a photo of me. I would like a few links....
• BIO
• TOURDATES
• BRENNA COYLE CRUISE
• MUSICAL TOUR OF IRELAND
• CONTACT
• VIDEO
• GALLERY
• CONTACT
• MAILING LIST
• STORE
Nice to have
• we'll see!

```html
<!DOCTYPE html>
<html lang="en">
<head>
<meta charset="utf-8">
<title>Brenna Coyle – Irish Musician</title>
<link rel="stylesheet" href="https://fonts.googleapis.com/css2?family=Raleway:wght@500;600;700;800&family=Open+Sans:wght@400;600;700&display=swap">
<style>
:root{
  --ink:#1c1c1c;
  --ink-soft:#3a3a3a;
  --text:#555555;
  --paper:#ffffff;
  --row:#efefef;
  --band:#232323;
  --band-deep:#151515;
  --muted:#8a8a8a;
  --header:#e4e5e7;
  --hero-a:#0e1a22;
  --hero-b:#5b6f7c;
}
*{box-sizing:border-box;margin:0;padding:0}
html,body{width:1200px;height:3041px;overflow:hidden}
body{position:relative;background:var(--paper);font-family:"Open Sans",Arial,sans-serif;color:var(--text)}
.abs{position:absolute}
.section-title{position:absolute;left:0;width:1200px;text-align:center;font-family:"Raleway",Arial,sans-serif;font-weight:800;font-size:34px;color:var(--ink);letter-spacing:.5px}
.title-dash{position:absolute;left:582px;width:36px;height:5px;background:var(--ink);border-radius:3px;transform:rotate(-6deg)}
.section-sub{position:absolute;left:0;width:1200px;text-align:center;font-size:12px;color:var(--ink-soft);text-transform:uppercase;letter-spacing:.3px}
.pill{position:absolute;background:var(--band);color:#fff;border-radius:24px;font-size:12px;font-weight:600;text-transform:uppercase;display:flex;align-items:center;justify-content:center}

/* header */
.site-header{position:absolute;left:0;top:0;width:1200px;height:112px;background:linear-gradient(#eeeff0,var(--header));z-index:2}
.brand{position:absolute;left:112px;top:30px;display:flex;align-items:center;gap:14px}
.brand-mark{width:40px;height:40px;border-radius:50%;background:var(--ink)}
.brand-name{font-family:"Raleway",Arial,sans-serif;font-weight:700;color:var(--ink);font-size:17px;line-height:20px;letter-spacing:.5px}
.brand-name small{display:block;font-size:11px;letter-spacing:1px}
.main-nav a{position:absolute;top:48px;font-size:14px;color:var(--ink);text-decoration:none;font-family:"Open Sans",Arial,sans-serif}
.nav-active::after{content:"";position:absolute;left:2px;top:28px;width:40px;height:5px;background:var(--ink);border-radius:3px;transform:rotate(6deg)}
.menu-btn{position:absolute;left:1076px;top:38px;width:36px;height:36px;border-radius:50%;background:var(--ink);display:flex;flex-direction:column;align-items:center;justify-content:center;gap:3px}
.menu-btn span{width:14px;height:2px;background:#fff}

/* hero */
.hero{position:absolute;left:0;top:112px;width:1200px;height:450px;background:radial-gradient(ellipse at 70% 10%,#aab8c1 0%,var(--hero-b) 30%,var(--hero-a) 85%)}
.hero-portrait{position:absolute;left:497px;top:90px;width:354px;height:360px;border-radius:170px 170px 0 0;background:linear-gradient(#6b4a34,#3a2a22 60%,#1e1a1a)}
.hero-title{position:absolute;left:122px;top:182px;font-family:"Raleway",Arial,sans-serif;font-weight:700;font-size:50px;color:#fff}
.hero-sub{position:absolute;left:122px;top:270px;width:380px;font-size:20px;font-weight:700;line-height:30px;color:#fff}
.hero-prev{position:absolute;left:40px;top:220px}

/* bio */
.bio-text{position:absolute;left:142px;top:680px;width:916px;font-size:11.5px;line-height:24px;text-align:center;color:var(--ink-soft)}

/* video */
.video{position:absolute;left:0;top:922px;width:1200px;height:513px;background:radial-gradient(ellipse at 30% 10%,#8d8d8d 0%,#3b3b3b 30%,#0b0b0b 75%)}
.video-thumb{position:absolute;left:340px;top:130px;width:520px;height:322px;background:linear-gradient(135deg,#8b6a4f,#4b3426 55%,#241a15);border:2px solid #ccc}
.play{position:absolute;left:230px;top:131px;width:60px;height:60px;border-radius:50%;background:rgba(255,255,255,.55);display:flex;align-items:center;justify-content:center}
.video-arrow{position:absolute;top:270px;width:44px;height:44px;border-radius:50%;background:rgba(255,255,255,.9);display:flex;align-items:center;justify-content:center}

/* tour */
.tour-row{position:absolute;left:162px;width:882px;height:97px;background:var(--row)}
.tour-date{position:absolute;left:6px;top:6px;width:110px;height:85px;background:var(--band);color:#fff;text-align:center}
.tour-day{font-family:"Raleway",Arial,sans-serif;font-weight:700;font-size:32px;line-height:32px;margin-top:12px}
.tour-month{font-size:15px;margin-top:6px}
.tour-name{position:absolute;left:164px;top:24px;font-family:"Raleway",Arial,sans-serif;font-weight:700;font-size:15px;color:var(--ink-soft)}
.tour-place{position:absolute;left:168px;top:58px;font-size:12px;color:var(--ink-soft)}
.tour-row .pill{left:714px;top:26px;width:140px;height:44px}

/* newsletter */
.newsletter{position:absolute;left:0;top:2102px;width:1200px;height:102px;background:var(--band)}
.nl-title{position:absolute;left:243px;top:26px;color:#fff;font-size:16px;font-weight:600}
.nl-sub{position:absolute;left:243px;top:52px;color:#fff;font-size:16px}
.nl-form{position:absolute;left:630px;top:30px;width:430px;height:42px;border-radius:21px;background:#fff}
.nl-form span{position:absolute;left:22px;top:12px;font-size:12px;color:#555}
.nl-form b{position:absolute;right:0;top:0;width:128px;height:42px;border-radius:21px;background:#666;color:#fff;font-weight:400;font-size:15px;display:flex;align-items:center;justify-content:center}

/* reviews */
.quote{position:absolute;left:233px;top:2358px;width:736px;text-align:center;font-size:12.5px;line-height:24px;color:var(--ink-soft)}
.reviewer{position:absolute;left:537px;top:2501px;width:126px;height:126px;transform:rotate(45deg);background:linear-gradient(135deg,#9a9a9a,#4d4d4d);border:3px solid #fff;box-shadow:0 0 0 1px #ccc}
.dot{position:absolute;top:2557px;width:14px;height:14px;border-radius:50%;border:1px solid #bbb}
.reviewer-name{position:absolute;left:0;top:2698px;width:1200px;text-align:center;font-weight:700;font-size:15px;color:var(--ink)}

/* contacts */
.contacts{position:absolute;left:0;top:2761px;width:1200px;height:235px;background:var(--band)}
.contacts .section-title{color:#fff;top:22px}
.contacts .title-dash{background:#fff;top:74px}
.touch{position:absolute;left:0;top:102px;width:1200px;text-align:center;color:#ddd;font-size:11px}
.social{position:absolute;top:134px;width:34px;height:34px;border-radius:50%;background:#0c0c0c}
.divider{position:absolute;top:118px;width:1px;height:100px;background:#444}
.c-line{position:absolute;color:#eee;font-size:12px;display:flex;align-items:center;gap:10px}
.site-footer{position:absolute;left:0;top:2996px;width:1200px;height:45px;background:var(--band-deep);color:#ddd;font-size:11px;text-align:center;line-height:45px}
</style>
</head>
<body>

<header class="site-header">
  <div class="brand">
    <div class="brand-mark"></div>
    <div class="brand-name">BRENNA COYLE'S<small>MUSICAL TOUR OF IRELAND</small></div>
  </div>
  <nav class="main-nav">
    <a class="nav-active" style="left:462px">Home</a>
    <a style="left:528px">Bio</a>
    <a style="left:576px">Tourdates</a>
    <a style="left:667px">Brenna Coyle Cruise</a>
    <a style="left:828px">Musical Tour Of Ireland</a>
    <a style="left:996px">Contact</a>
  </nav>
  <div class="menu-btn"><span></span><span></span><span></span></div>
</header>

<section class="hero" role="img" aria-label="Concert crowd with raised hands under stage lights">
  <div class="hero-portrait" role="img" aria-label="Portrait of Brenna Coyle"></div>
  <svg class="hero-prev" width="16" height="30" viewBox="0 0 16 30"><path d="M14 2 L3 15 L14 28" fill="none" stroke="#fff" stroke-width="2"/></svg>
  <h1 class="hero-title">Brenna Coyle</h1>
  <p class="hero-sub">Irish musician who plays the tin whistle and the flute</p>
</section>

<section class="bio">
  <h2 class="section-title" style="top:604px">BIO</h2>
  <div class="title-dash" style="top:655px"></div>
  <p class="bio-text">BRENNA COYLE is considered one of the greatest musicians and personalities in the history of Irish music in America. She was born in the Bronx, New York of Irish parents, and she is the second oldest of seven children raised in a musical household. Her mother Maura hails from Kilbrack, County Clare and her father Declan, an All-Ireland Champion accordion player, was a native of Ballinrue, County Galway. Brenna was exposed to the finest Irish traditional music early in her life, listening to her father and his friends play music at family gatherings and social events. She began taking lessons from legendary flutist Tom Farrelly, and within a few short years she won the All-Ireland Championship on both the concert flute and tin whistle. In 1984, Brenna became the first American to win the coveted Senior All-Ireland Championship on the whistle.</p>
  <div class="pill" style="left:530px;top:828px;width:140px;height:46px">Read more</div>
</section>

<section class="video" role="img" aria-label="Dark concert stage with spotlights and smoke">
  <h2 class="section-title" style="top:50px;color:#fff">VIDEO</h2>
  <div class="video-thumb" role="img" aria-label="Video still of the Gather the Willows ensemble with instruments">
    <div class="play"><svg width="22" height="24" viewBox="0 0 22 24"><path d="M3 2 L20 12 L3 22Z" fill="#fff"/></svg></div>
  </div>
  <div class="video-arrow" style="left:316px"><svg width="20" height="18" viewBox="0 0 20 18"><path d="M10 2 L3 9 L10 16 M17 2 L10 9 L17 16" fill="none" stroke="#555" stroke-width="2"/></svg></div>
  <div class="video-arrow" style="left:838px"><svg width="20" height="18" viewBox="0 0 20 18"><path d="M3 2 L10 9 L3 16 M10 2 L17 9 L10 16" fill="none" stroke="#555" stroke-width="2"/></svg></div>
</section>

<section class="tour">
  <h2 class="section-title" style="top:1494px">TOUR DATES</h2>
  <div class="title-dash" style="top:1548px"></div>
  <p class="section-sub" style="top:1577px">Find out where the next show begin</p>

  <div class="tour-row" style="top:1615px">
    <div class="tour-date"><div class="tour-day">21</div><div class="tour-month">OCT 14</div></div>
    <div class="tour-name">CONTRARY TO POPULAR BELIEF,</div>
    <div class="tour-place">Some Night Club &nbsp;/&nbsp; Default City &nbsp;/&nbsp; Unknown address</div>
    <div class="pill">Read more</div>
  </div>
  <div class="tour-row" style="top:1726px">
    <div class="tour-date"><div class="tour-day">17</div><div class="tour-month">NOV 14</div></div>
    <div class="tour-name">CONTRARY TO POPULAR BELIEF,</div>
    <div class="tour-place">Some Night Club &nbsp;/&nbsp; Default City &nbsp;/&nbsp; Unknown address</div>
    <div class="pill">Read more</div>
  </div>
  <div class="tour-row" style="top:1837px">
    <div class="tour-date"><div class="tour-day">28</div><div class="tour-month">NOV 14</div></div>
    <div class="tour-name">CONTRARY TO POPULAR BELIEF,</div>
    <div class="tour-place">Some Night Club &nbsp;/&nbsp; Default City &nbsp;/&nbsp; Unknown address</div>
    <div class="pill">Read more</div>
  </div>
  <div class="tour-row" style="top:1948px">
    <div class="tour-date"><div class="tour-day">15</div><div class="tour-month">NOV 14</div></div>
    <div class="tour-name">CONTRARY TO POPULAR BELIEF,</div>
    <div class="tour-place">Some Night Club &nbsp;/&nbsp; Default City &nbsp;/&nbsp; Unknown address</div>
    <div class="pill">Read more</div>
  </div>
</section>

<section class="newsletter">
  <svg class="abs" style="left:126px;top:12px" width="92" height="80" viewBox="0 0 92 80"><g transform="rotate(-20 46 40)" fill="none" stroke="#4a4a4a" stroke-width="3"><rect x="12" y="18" width="68" height="46"/><path d="M12 18 L46 46 L80 18"/></g></svg>
  <div class="nl-title">JOIN OUR NEWSLETTER</div>
  <div class="nl-sub">Lorem ipsum dolor sit amet, consectetur</div>
  <div class="nl-form"><span>Enter your E - mail</span><b>SUBSCRIBE</b></div>
</section>

<section class="reviews">
  <h2 class="section-title" style="top:2252px">REVIEWS</h2>
  <div class="title-dash" style="top:2306px"></div>
  <p class="section-sub" style="top:2327px">From music experts and critics</p>
  <p class="quote">“When distinguished tin whistle or flute players over the past quarter of a century come to mind, Irish traditional music aficionados invariably will add Brenna Coyle's name to the list. Her music is pure art, compelling and creative, vibrant and virtuosic. It is filled with style, substance, sensitivity and soul.”</p>
  <svg class="abs" style="left:394px;top:2554px" width="20" height="20" viewBox="0 0 20 20"><path d="M10 3 L3 10 L10 17 M17 3 L10 10 L17 17" fill="none" stroke="#999" stroke-width="1.5"/></svg>
  <div class="dot" style="left:426px;background:var(--ink);border-color:var(--ink)"></div>
  <div class="dot" style="left:450px"></div>
  <div class="reviewer" role="img" aria-label="Photo of reviewer Owen Delaney"></div>
  <div class="dot" style="left:734px"></div>
  <div class="dot" style="left:758px"></div>
  <svg class="abs" style="left:786px;top:2554px" width="20" height="20" viewBox="0 0 20 20"><path d="M3 3 L10 10 L3 17 M10 3 L17 10 L10 17" fill="none" stroke="#999" stroke-width="1.5"/></svg>
  <p class="reviewer-name">Owen Delaney, The Celtic Ledger</p>
</section>

<section class="contacts">
  <h2 class="section-title">CONTACTS</h2>
  <div class="title-dash"></div>
  <p class="touch">GET IN TOUCH</p>
  <div class="social" style="left:482px"></div>
  <div class="social" style="left:533px"></div>
  <div class="social" style="left:585px"></div>
  <div class="social" style="left:636px"></div>
  <div class="social" style="left:688px"></div>
  <div class="divider" style="left:462px"></div>
  <div class="divider" style="left:744px"></div>
  <div class="c-line" style="left:186px;top:138px">
    <svg width="16" height="16" viewBox="0 0 16 16"><path d="M3 1 L6 1 L7 5 L5 6 Q6 9 10 11 L11 9 L15 10 L15 13 Q14 15 12 15 Q2 12 1 3 Q1 1 3 1Z" fill="#fff"/></svg>
    <span>Phone : 1800 555 014</span>
  </div>
  <div class="c-line" style="left:186px;top:172px">
    <svg width="18" height="14" viewBox="0 0 18 14"><rect x="1" y="1" width="16" height="12" fill="#fff"/><path d="M1 1 L9 8 L17 1" fill="none" stroke="#232323" stroke-width="1.5"/></svg>
    <span>E-mail : book@brennacoylevoyage-example.com</span>
  </div>
  <div class="c-line" style="left:788px;top:138px"><span>Phone : 1800 555 014</span></div>
  <div class="c-line" style="left:788px;top:172px"><span>E-mail : book@brennacoylevoyage-example.com</span></div>
</section>

<footer class="site-footer">Copyright @ 2016. Brenna Coyle. All Rights Reserved.</footer>

</body>
</html>
```